Children’s entertainer/balloon artist Website Home Page and custom landing page

I need a home page design for the home page of a children and family entertainer/balloon twister’s website. I also need a custom landing page for family theatre shows performed by the same entertainer.
It will be a Wordpress website and I need the final artwork in a layer Photoshop file with all the layers clearly named and labeled.

Target Market(s)

The site visitors are mainly mums, aged between early 20’s and late 30’s. Other visitors will included companies for Christmas functions, and event organisers for corporate functions.

Industry/Entity Type

Entertainment

Number of Pages Required

2 page

Font styles to use
Sans Serif

Colors
34a6d7
f37122

Requirements
Must have
• Layout
• I have included a wireframe for the home page layout and the custom landing page for your reference. This is a guide only and I welcome your interpretation with the rough layout provided.
• This website needs to look good on all devices as it will be fully responsive.
• It needs to include a footer area on the page, that has social media and a call to action area included.
• Colours
• The main colours for the site is:
• orange (call to action colour)
• ff6800
• blue/turquoise
• 42abc3
• Pictures
• I have included images of the entertainer/balloon artist for you to use/take inspiration from.
• These images will be included on the website. I want to show lots of people having fun.
• I would like to have elements of the logo used in isolation across the website
• i.e. the octopus figure to be included in the footer or the bird element to be included in the testimonial slider etc.
• Elements to include
• Note: use the images of the entertainer in the boxes on the home page (balloon shows, balloon twisting, balloon workshops, theatre shows (the three little balloon pigs on his head)
Nice to have
Should not have
• Element to avoid
• Stock imagery of balloon sculptures - use images provided.

```html
<!DOCTYPE html>
<html lang="en">
<head>
<meta charset="utf-8">
<title>Robin – Theater Artist &amp; Balloon Artist</title>
<link href="https://fonts.googleapis.com/css2?family=Roboto+Slab:wght@400;700&family=Open+Sans:wght@400;600;700&display=swap" rel="stylesheet">
<style>
:root{
  --orange:#f37122;
  --blue:#34a6d7;
  --navy:#16213f;
  --hero-top:#4a5fb4;
  --hero-bottom:#2f3f8c;
  --parchment:#e9d9b4;
  --ink:#3b2f22;
  --text:#5a4b3a;
  --white:#ffffff;
  --footer:#2a2a2a;
  --footer-dark:#1c1c1c;
  --line:#c9b58c;
}
*{box-sizing:border-box;margin:0;padding:0}
html,body{width:1200px;height:2588px;overflow:hidden}
body{font-family:"Open Sans",Arial,sans-serif;color:var(--text);background:var(--parchment);position:relative}
section,header,footer,nav.topnav{position:absolute;left:0;width:1200px}

/* nav */
.topnav{top:0;height:30px;background:var(--navy);display:flex;align-items:center;padding-left:64px;gap:38px;z-index:3}
.topnav a{color:var(--white);font-size:14px;font-weight:700;text-decoration:none;text-transform:uppercase;letter-spacing:.5px;white-space:nowrap}
.topnav a.active{border-bottom:2px solid var(--white)}

/* hero */
.hero{top:0;height:740px;background:linear-gradient(180deg,var(--hero-top),var(--hero-bottom));overflow:hidden}
.hero-photo{position:absolute;right:0;top:30px;width:720px;height:710px;background:radial-gradient(circle at 55% 40%,#e6b8a0 0,#c89b8a 14%,#5a6fc2 40%,var(--hero-bottom) 80%)}
.brand{position:absolute;left:175px;top:160px;display:flex;align-items:center;gap:12px}
.brand-mark{width:40px;height:40px;background:var(--orange)}
.brand-name{font-family:"Roboto Slab",Georgia,serif;font-weight:700;font-size:24px;color:var(--white);white-space:nowrap}
.hero-name{position:absolute;left:140px;top:370px;font-family:"Roboto Slab",Georgia,serif;font-size:76px;font-weight:400;color:var(--white);letter-spacing:2px;line-height:90px}
.hero-role{position:absolute;left:140px;top:470px;font-size:22px;color:var(--white);font-weight:600;white-space:nowrap}
.btn-book{position:absolute;left:175px;top:520px;width:180px;height:60px;border:3px solid var(--white);color:var(--white);font-weight:700;font-size:18px;display:flex;align-items:center;justify-content:center}

/* parchment sections */
.paper{background:linear-gradient(180deg,#efe0bd,#e2cfa3)}
.about{top:740px;height:340px}
.section-title{font-family:"Roboto Slab",Georgia,serif;font-weight:700;font-size:30px;color:var(--ink);text-transform:uppercase}
.section-title .hl{color:var(--orange)}
.about .section-title{position:absolute;left:80px;top:40px}
.about p{position:absolute;left:80px;top:100px;width:610px;font-size:15px;line-height:25px}
.btn-line{position:absolute;border:2px solid var(--orange);color:var(--ink);font-weight:700;font-size:14px;display:flex;align-items:center;justify-content:center;background:var(--white);white-space:nowrap}
.about .btn-line{left:80px;top:270px;width:100px;height:40px}
.filmstrip{position:absolute;left:740px;top:50px;width:400px;height:230px;background:#1e1e1e;border-radius:4px}
.filmstrip .frame{position:absolute;left:22px;top:22px;width:356px;height:186px;background:linear-gradient(135deg,#e9b1b1,#c97e86 50%,#8e5f58)}
.filmstrip .holes{position:absolute;left:8px;right:8px;height:10px;background:repeating-linear-gradient(90deg,#e8e8e8 0 12px,transparent 12px 26px)}

/* three columns */
.columns{top:1080px;height:460px;border-top:1px solid var(--line)}
.col{position:absolute;top:40px}
.col h3{font-family:"Roboto Slab",Georgia,serif;font-size:24px;font-weight:700;color:var(--ink);text-transform:uppercase;border-bottom:2px solid var(--line);padding-bottom:8px;white-space:nowrap}
.col h3 .hl{color:var(--orange)}
.events{left:80px;width:370px}
.cal{margin-top:18px;width:260px;background:var(--white);border:1px solid var(--line)}
.cal-head{background:var(--orange);color:var(--white);font-family:"Roboto Slab",Georgia,serif;font-weight:700;font-size:22px;text-align:center;padding:8px 0}
.cal table{width:100%;border-collapse:collapse;font-size:12px;text-align:center}
.cal th{font-weight:700;padding:6px 0;color:var(--ink)}
.cal td{padding:6px 0;color:var(--text)}
.cal td.mark{background:var(--blue);color:var(--white)}
.cal-tag{position:absolute;left:210px;top:272px;background:var(--blue);color:var(--white);font-size:11px;font-weight:700;padding:5px 8px;white-space:nowrap}
.news{left:490px;width:300px}
.news-item{display:flex;gap:14px;margin-top:20px}
.news-date{width:46px;flex:none;text-align:center}
.news-date .d{background:var(--orange);color:var(--white);font-family:"Roboto Slab",Georgia,serif;font-weight:700;font-size:22px;padding:4px 0}
.news-date .m{background:var(--blue);color:var(--white);font-size:11px;font-weight:700;padding:2px 0}
.news-item h4{font-size:14px;font-weight:700;color:var(--ink)}
.news-item p{font-size:12px;line-height:18px}
.news-pager{position:absolute;right:0;top:4px;display:flex;gap:4px}
.news-pager span{width:20px;height:20px;background:var(--white);border:1px solid var(--line)}
.view-all{margin-top:16px;text-align:right;font-size:13px;font-weight:700;color:var(--orange)}
.newsletter{left:840px;width:290px}
.newsletter p{font-size:13px;line-height:20px;margin-top:16px}
.field{height:36px;background:var(--white);border:1px solid var(--line);margin-top:12px;font-size:12px;color:#999;padding:9px 10px}
.newsletter .btn-line{position:static;width:100px;height:36px;margin-top:14px}

/* testimonials */
.testimonials{top:1540px;height:440px;border-top:1px solid var(--line)}
.testimonials .section-title{text-align:center;margin-top:36px}
.avatar{position:absolute;left:560px;top:100px;width:80px;height:80px;border-radius:50%;background:radial-gradient(circle,#f1c9b0,#b98064);border:4px solid var(--white)}
.quote-badge{position:absolute;left:618px;top:158px;width:28px;height:28px;border-radius:50%;background:var(--orange)}
.testimonials blockquote{position:absolute;left:210px;top:210px;width:780px;text-align:center;font-size:15px;line-height:25px}
.testimonials cite{position:absolute;left:0;width:1200px;top:320px;text-align:center;font-style:normal;font-size:15px;font-weight:700;color:var(--ink)}
.testimonials cite span{color:var(--orange);font-weight:400}
.arrow{position:absolute;top:220px;width:46px;height:46px;border-radius:50%;background:#333}
.arrow.left{left:110px}.arrow.right{right:110px}
.arrow svg{position:absolute;left:13px;top:13px}

/* contact */
.contact{top:1980px;height:440px;border-top:1px solid var(--line)}
.contact .section-title{text-align:center;margin-top:36px}
.form{position:absolute;left:80px;top:110px;width:640px}
.form .row{display:flex;gap:20px}
.form .field{flex:1}
.form .area{height:110px}
.form .btns{display:flex;gap:20px;margin-top:20px}
.form .btn-line{position:static;height:40px}
.divider{position:absolute;left:750px;top:110px;width:2px;height:260px;background:var(--line)}
.info{position:absolute;left:820px;top:110px;width:330px}
.info-item{display:flex;align-items:center;gap:18px;margin-bottom:28px}
.info-icon{width:50px;height:50px;border-radius:50%;background:var(--orange);flex:none;display:flex;align-items:center;justify-content:center}
.info-item p{font-size:15px;line-height:22px;color:var(--ink)}
.info-item .big{font-size:24px;font-weight:700}

/* footer */
.site-footer{top:2420px;height:168px;background:var(--footer)}
.foot-nav{display:flex;justify-content:center;gap:36px;margin-top:34px}
.foot-nav a{color:var(--white);font-size:14px;font-weight:600;text-decoration:none;text-transform:uppercase}
.social{display:flex;justify-content:center;gap:16px;margin-top:24px}
.social span{width:34px;height:34px;border:2px solid #bbb}
.copy{position:absolute;bottom:0;width:1200px;height:34px;background:var(--footer-dark);color:#aaa;font-size:12px;text-align:center;line-height:34px}
</style>
</head>
<body>

<header class="hero">
  <div class="hero-photo" role="img" aria-label="Photo of the entertainer surrounded by colourful balloon sculptures"></div>
  <div class="brand"><span class="brand-mark"></span><span class="brand-name">Twistabout Shows</span></div>
  <h1 class="hero-name">ROBIN</h1>
  <div class="hero-role">Theater Artist &nbsp;•&nbsp; Balloon Artist</div>
  <div class="btn-book">BOOK ME NOW</div>
</header>

<nav class="topnav">
  <a class="active">Home</a><a>About Me</a><a>Corporate Shows</a><a>Private Functions</a><a>Directing</a><a>Reviews</a><a>Contact Me</a>
</nav>

<section class="about paper">
  <h2 class="section-title">About My Theater Performance</h2>
  <p>Lorem ipsum dolor sit amet, consectetur adipiscing elit, sed do eiusmod tempor incididunt ut labore et dolore magna aliqua. Ut enim ad minim veniam, quis nostrud exercitation ullamco laboris nisi ut aliquip ex ea commodo consequat. Duis aute irure dolor in reprehenderit in voluptate velit esse cillum dolore eu fugiat nulla pariatur. Excepteur sint occaecat cupidatat non proident, sunt in culpa qui officia deserunt mollit anim id est laborum.</p>
  <div class="btn-line">READ ALL</div>
  <div class="filmstrip">
    <div class="holes" style="top:6px"></div>
    <div class="frame" role="img" aria-label="Photo of the entertainer wearing three balloon pigs on his head"></div>
    <div class="holes" style="bottom:6px"></div>
  </div>
</section>

<section class="columns paper">
  <div class="col events">
    <h3>Upcoming <span class="hl">Events</span></h3>
    <div class="cal">
      <div class="cal-head">OCTOBER 2015</div>
      <table>
        <tr><th>SUN</th><th>MON</th><th>TUE</th><th>WED</th><th>THR</th><th>FRI</th><th>SAT</th></tr>
        <tr><td></td><td></td><td></td><td></td><td>1</td><td>2</td><td>3</td></tr>
        <tr><td>4</td><td>5</td><td>6</td><td>7</td><td>8</td><td>9</td><td>10</td></tr>
        <tr><td>11</td><td>12</td><td>13</td><td>14</td><td>15</td><td>16</td><td>17</td></tr>
        <tr><td>18</td><td>19</td><td>20</td><td>21</td><td>22</td><td>23</td><td>24</td></tr>
        <tr><td>25</td><td>26</td><td>27</td><td>28</td><td class="mark">29</td><td>30</td><td>31</td></tr>
      </table>
    </div>
    <div class="cal-tag">COMEDY SHOW</div>
  </div>

  <div class="col news">
    <h3>Latest <span class="hl">News</span></h3>
    <div class="news-pager"><span></span><span></span></div>
    <div class="news-item"><div class="news-date"><div class="d">30</div><div class="m">OCT</div></div><div><h4>Lorem Ipsum Dolor</h4><p>Nam liber tempor cum soluta nobis eleifend option congue.</p></div></div>
    <div class="news-item"><div class="news-date"><div class="d">30</div><div class="m">OCT</div></div><div><h4>Lorem Ipsum Dolor</h4><p>Nam liber tempor cum soluta nobis eleifend option congue.</p></div></div>
    <div class="news-item"><div class="news-date"><div class="d">30</div><div class="m">OCT</div></div><div><h4>Lorem Ipsum Dolor</h4><p>Nam liber tempor cum soluta nobis eleifend option congue.</p></div></div>
    <div class="view-all">VIEW ALL &gt;&gt;</div>
  </div>

  <div class="col newsletter">
    <h3>Newsletter <span class="hl">Signup</span></h3>
    <p>Signup To Our Newsletter For Weekly Updates, Fill The Form and It's done.</p>
    <div class="field">Type your Name</div>
    <div class="field">Type your Email</div>
    <div class="btn-line">SUBMIT</div>
  </div>
</section>

<section class="testimonials paper">
  <h2 class="section-title">What My Customers Say</h2>
  <div class="avatar" role="img" aria-label="Customer portrait"></div>
  <div class="quote-badge"></div>
  <div class="arrow left"><svg width="20" height="20" viewBox="0 0 20 20"><path d="M13 3 6 10l7 7" fill="none" stroke="#fff" stroke-width="3"/></svg></div>
  <blockquote>Sed ut perspiciatis unde omnis iste natus error sit voluptatem accusantium doloremque laudantium, totam rem aperiam, eaque ipsa quae ab illo inventore veritatis et quasi architecto beatae vitae dicta sunt explicabo. Nemo enim ipsam voluptatem quia voluptas sit aspernatur aut odit aut fugit.</blockquote>
  <cite>LAURA BENNETT <span>| Party Planner</span></cite>
  <div class="arrow right"><svg width="20" height="20" viewBox="0 0 20 20"><path d="M7 3l7 7-7 7" fill="none" stroke="#fff" stroke-width="3"/></svg></div>
</section>

<section class="contact paper">
  <h2 class="section-title">Contact The <span class="hl">Entertainer</span></h2>
  <div class="form">
    <div class="row"><div class="field">First Name</div><div class="field">Last Name</div></div>
    <div class="row"><div class="field">Phone</div><div class="field">Email</div></div>
    <div class="field area">Message</div>
    <div class="btns"><div class="btn-line" style="width:100px">SEND</div><div class="btn-line" style="width:200px">REQUEST A CALL BACK</div></div>
  </div>
  <div class="divider"></div>
  <div class="info">
    <div class="info-item"><div class="info-icon"><svg width="22" height="26" viewBox="0 0 22 26"><path d="M11 1a9 9 0 0 0-9 9c0 7 9 15 9 15s9-8 9-15a9 9 0 0 0-9-9z" fill="#fff"/><circle cx="11" cy="10" r="3.5" fill="#f37122"/></svg></div><p><strong>Twistabout Shows</strong><br>Lorem Ipsum, Dolor Sinit,<br>City Code - 123456</p></div>
    <div class="info-item"><div class="info-icon"><svg width="22" height="22" viewBox="0 0 24 24"><path d="M6.6 10.8a15 15 0 0 0 6.6 6.6l2.2-2.2c.3-.3.7-.4 1-.2 1.1.4 2.3.6 3.6.6.6 0 1 .4 1 1V20c0 .6-.4 1-1 1A17 17 0 0 1 3 4c0-.6.4-1 1-1h3.5c.6 0 1 .4 1 1 0 1.3.2 2.5.6 3.6.1.3 0 .7-.2 1z" fill="#fff"/></svg></div><p class="big">123-456-7890</p></div>
    <div class="info-item"><div class="info-icon"><svg width="24" height="18" viewBox="0 0 24 18"><rect x="1" y="1" width="22" height="16" fill="#fff"/><path d="M1 1l11 9 11-9" fill="none" stroke="#f37122" stroke-width="2"/></svg></div><p>info@twistaboutshows.com</p></div>
  </div>
</section>

<footer class="site-footer">
  <nav class="foot-nav"><a>Home</a><a>About Me</a><a>Corporate Shows</a><a>Private Functions</a><a>Directing</a><a>Reviews</a><a>Contact Me</a></nav>
  <div class="social"><span></span><span></span><span></span><span></span></div>
  <div class="copy">Copyright Twistabout Shows &nbsp;|&nbsp; All Rights Reserved</div>
</footer>

</body>
</html>
```